Round Label Sticker 2.5-3 inch diameter

We need a design for a sticker to distribute for more brand recognition and product outreach.
My company The Brisk Lark Company Ltd. Specializes in working with people with diabetes. My products are made for diabetics because they have no added sugars, high in protein and fiber and each serving is lower than 5% daily value of carbohydrates.
I am a dietitian and my dad passed away from diabetes. I have created a growing food and beverage line that will give more joy into a diabetic's life while providing more food options that make them feel happy instead of guilty when they eat it.
I am teaching cooking classes to promote my products as well as doing exhibits and events. I want to give away a sticker to people that reads "I'm too sweet for sugar!" and somewhere on it would be my logo as well as my website info. www.brisklark-example.com
The sticker should make people smile and warm as well as draw interest to my product line.
Target Market(s)
Diabetes and people who do not want added sugars in their food
Industry/Entity Type
Food Store
Requirements
Must have
- my logo and website

```html
<!DOCTYPE html>
<html lang="en">
<head>
<meta charset="utf-8">
<title>I'm too sweet for sugar! – Brisk Lark sticker</title>
<link rel="stylesheet" href="https://fonts.googleapis.com/css2?family=Caveat+Brush&family=Kaushan+Script&family=Quicksand:wght@500&display=swap">
<style>
  :root {
    --paper: #ffffff;
    --rind: #a9d47c;
    --flesh-light: #9cc86c;
    --flesh-dark: #86b45a;
    --ink: #ffffff;
  }
  html, body {
    margin: 0;
    padding: 0;
    width: 1200px;
    height: 1157px;
    overflow: hidden;
    background: var(--paper);
  }
  .sticker {
    display: block;
    width: 1200px;
    height: 1157px;
  }
  .brand-name {
    font-family: "Caveat Brush", cursive;
    font-size: 64px;
    letter-spacing: 4px;
    fill: var(--ink);
  }
  .headline-script {
    font-family: "Kaushan Script", cursive;
    fill: var(--ink);
  }
  .headline-caps {
    font-family: "Caveat Brush", cursive;
    fill: var(--ink);
  }
  .web-address {
    font-family: "Quicksand", sans-serif;
    font-weight: 500;
    font-size: 52px;
    letter-spacing: 2px;
    fill: var(--ink);
  }
</style>
</head>
<body>
<svg class="sticker" viewBox="0 0 1200 1157" xmlns="http://www.w3.org/2000/svg">
  <defs>
    <radialGradient id="lime-flesh" cx="50%" cy="50%" r="50%">
      <stop offset="0%" stop-color="var(--flesh-dark)"/>
      <stop offset="70%" stop-color="var(--flesh-light)"/>
      <stop offset="100%" stop-color="var(--flesh-dark)"/>
    </radialGradient>
    <path id="address-arc" d="M 158 580 A 442 442 0 0 0 1042 580"/>
  </defs>

  <g class="lime-slice" role="img" aria-label="Illustration of a sliced lime seen from above">
    <circle cx="600" cy="580" r="546" fill="var(--rind)"/>
    <circle cx="600" cy="580" r="500" fill="url(#lime-flesh)"/>
  </g>

  <text class="brand-name" x="600" y="196" text-anchor="middle">BRISK LARK</text>

  <text class="headline-script" x="618" y="372" font-size="150" text-anchor="middle">I'm too</text>
  <text class="headline-caps" x="465" y="648" font-size="190" text-anchor="middle">SWEET</text>
  <text class="headline-script" x="810" y="640" font-size="190" text-anchor="middle">for</text>
  <text class="headline-caps" x="632" y="892" font-size="200" text-anchor="middle">SUGAR!</text>

  <text class="web-address">
    <textPath href="#address-arc" startOffset="50%" text-anchor="middle">www.brisklark-example.com</textPath>
  </text>
</svg>
</body>
</html>
```